Website re-design for Brightmoor LLC website ( has existing website )

Looking to do a complete re-design of Brightmoorllc. The existing website is dated and built in wordpress. The new website will not be wordpress. The project folder includes an overview.txt file with details on the project. The file also contains a list of websites that he/she likes which I am sure is very helpful .
Number of Pages Required
1 page

```html
<!DOCTYPE html>
<html lang="en">
<head>
<meta charset="utf-8">
<title>Brightmoor LLC – Shoreline Care</title>
<link rel="stylesheet" href="https://fonts.googleapis.com/css2?family=Oswald:wght@300;400;500;600;700&family=Roboto:wght@300;400;500;700&display=swap">
<style>
:root{
  --blue:#0b6fc0;
  --blue-dark:#0a5da3;
  --ink:#333333;
  --text:#8a8a8a;
  --light:#f3f4f5;
  --services-bg:#e8edf1;
  --footer:#343434;
  --footer-dark:#2b2b2b;
  --white:#ffffff;
}
*{box-sizing:border-box;margin:0;padding:0}
html,body{width:1200px;height:4224px;overflow:hidden;background:var(--white)}
body{font-family:'Roboto',sans-serif;color:var(--ink)}
.page{position:relative;width:1200px;height:4224px;overflow:hidden}
.abs{position:absolute}
.heading{font-family:'Oswald',sans-serif;text-transform:uppercase;color:var(--ink);font-size:40px;line-height:1}
.heading .light{font-weight:300;color:#666}
.heading .bold{font-weight:600}
.btn{position:absolute;display:flex;align-items:center;justify-content:center;background:var(--blue);color:var(--white);font-weight:700;font-size:14px;border-radius:26px;text-transform:uppercase;letter-spacing:.2px}
.underline{position:absolute;height:4px;width:59px;background:var(--blue);left:570px}

/* top bar */
.topbar{left:0;top:0;width:1200px;height:43px;background:var(--light);font-size:13px;color:#666}
.topbar .item{position:absolute;top:13px;display:flex;align-items:center;gap:8px}
.topbar .sep{position:absolute;top:0;width:1px;height:43px;background:#ddd}
.estimate{left:943px;top:2px;width:144px;height:39px;font-size:12px}

/* nav */
.nav{left:0;top:43px;width:1200px;height:75px;background:var(--white);border-bottom:1px solid #eee}
.logo{position:absolute;left:112px;top:8px;display:flex;align-items:center;gap:8px}
.logo .mark{width:60px;height:60px;border-radius:50%;background:var(--blue)}
.logo .name{font-family:'Roboto',sans-serif;font-weight:400;font-size:30px;color:var(--blue)}
.menu a{position:absolute;top:31px;font-size:12.5px;font-weight:700;color:#444;text-decoration:none;text-transform:uppercase}
.menu a.active{color:var(--blue);border-bottom:2px solid var(--blue);padding-bottom:2px}
.menu .dot{position:absolute;left:448px;top:13px;width:14px;height:14px;border-radius:50%;background:var(--blue)}

/* hero */
.hero{left:0;top:118px;width:1200px;height:644px}
.hero-line{left:600px;top:315px;width:3px;height:218px;background:var(--white)}
.hero-title{left:628px;top:330px;font-family:'Oswald',sans-serif;font-weight:600;font-size:40px;line-height:45px;color:var(--white);text-transform:uppercase}
.hero-sub{left:628px;top:430px;font-size:22px;color:var(--white)}
.hero-btn{left:628px;top:485px;width:154px;height:51px}
.arrow{position:absolute;width:36px;height:36px;border-radius:50%;background:var(--white);display:flex;align-items:center;justify-content:center;box-shadow:0 2px 6px rgba(0,0,0,.2)}
.arrow.outline{background:var(--white);border:2px solid var(--blue);box-shadow:none}

/* about */
.about-title{left:112px;top:862px}
.about-text{left:112px;top:943px;width:460px;font-size:13.5px;line-height:26px;color:var(--text);text-align:justify}
.about-text p+p{margin-top:10px}
.about-btn{left:112px;top:1190px;width:147px;height:50px}
.about-ring{left:627px;top:820px;width:462px;height:462px;border-radius:50%;border:6px solid var(--blue);background:var(--white)}
.about-photo{left:643px;top:836px;width:430px;height:430px;border-radius:50%;background:linear-gradient(180deg,#8fb0cf 0%,#5b86ad 45%,#3b6285 70%,#a9a49a 100%)}

/* services */
.services{left:0;top:1371px;width:1200px;height:1045px;background:linear-gradient(180deg,#eef1f3 0%,#e2e9ee 50%,#eef1f4 100%)}
.services-title{left:0;width:1200px;top:1425px;text-align:center}
.card{position:absolute;width:305px;height:362px}
.card .photo{position:absolute;left:0;top:0;width:305px;height:203px;border:2px solid var(--white)}
.card .body{position:absolute;left:8px;top:185px;width:289px;height:177px;background:var(--white);padding:14px 13px;box-shadow:0 1px 3px rgba(0,0,0,.06)}
.card .icon{position:absolute;left:13px;top:14px;width:76px;height:76px;background:var(--blue);display:flex;align-items:center;justify-content:center}
.card h3{position:absolute;left:110px;top:26px;font-size:16.5px;line-height:26px;font-weight:500;text-transform:uppercase;color:#222}
.card p{position:absolute;left:13px;top:101px;width:263px;font-size:13px;line-height:24px;color:var(--text);text-align:justify}
.card.featured .photo{border-color:var(--blue)}
.card.featured .body{background:var(--blue)}
.card.featured .icon{background:var(--white)}
.card.featured h3,.card.featured p{color:var(--white)}
.services-btn{left:498px;top:2307px;width:204px;height:51px}

/* gallery */
.gallery-title{left:0;width:1200px;top:2494px;text-align:center}
.shot{position:absolute;top:2583px;height:290px}
.handle{position:absolute;top:2707px;width:44px;height:44px;border-radius:50%;background:var(--white);display:flex;align-items:center;justify-content:center;box-shadow:0 1px 4px rgba(0,0,0,.2)}
.tag{position:absolute;top:2711px;width:86px;height:34px;background:var(--white);font-size:13px;font-weight:700;display:flex;align-items:center;justify-content:center}

/* innovators */
.innov{left:0;top:2963px;width:1200px;height:445px}
.innov-title{left:681px;top:3050px;font-family:'Oswald',sans-serif;color:var(--white);font-size:38px;line-height:44px;text-transform:uppercase}
.innov-title b{font-weight:600}
.innov-title span{font-weight:400}
.innov-line{left:681px;top:3142px;width:56px;height:3px;background:var(--white)}
.innov-text{left:681px;top:3178px;width:408px;font-size:13.5px;line-height:25.5px;color:var(--white);text-align:justify}

/* testimonials */
.testi-title{left:0;width:1200px;top:3497px;text-align:center;font-weight:600}
.avatar-ring{left:166px;top:3552px;width:200px;height:200px;border-radius:50%;border:5px solid var(--blue);background:var(--white)}
.avatar{left:178px;top:3564px;width:176px;height:176px;border-radius:50%;background:linear-gradient(180deg,#9ec2de 0%,#6d8fa8 55%,#3a4a57 100%)}
.quote-badge{left:165px;top:3550px;width:66px;height:66px;border-radius:50%;background:var(--blue);border:4px solid var(--white);display:flex;align-items:center;justify-content:center}
.testi-text{left:451px;top:3582px;width:585px;font-size:14.5px;line-height:26px;color:var(--text)}
.testi-name{left:451px;top:3673px;font-size:15px;font-weight:700;color:var(--blue);text-transform:uppercase}
.testi-place{left:451px;top:3702px;font-size:15px;font-weight:500;color:#333}
.dots{left:567px;top:3760px;display:flex;gap:6px}
.dots i{width:11px;height:11px;border-radius:50%;background:#d6d6d6}
.dots i.on{background:var(--blue)}

/* footer */
.footer{left:0;top:3842px;width:1200px;height:382px;background:var(--footer)}
.footer-right{left:763px;top:3842px;width:437px;height:382px;background:var(--footer-dark)}
.foot-h{position:absolute;top:3900px;font-size:15px;font-weight:700;color:var(--white);text-transform:uppercase}
.foot-list{position:absolute;top:3943px;list-style:none}
.foot-list li{display:flex;align-items:center;gap:16px;height:34px;font-size:13px;color:var(--white)}
.foot-list li i{width:13px;height:13px;border-radius:50%;background:var(--blue);display:block}
.contact{position:absolute;left:495px;display:flex;align-items:center;gap:24px;font-size:13px;color:var(--white);line-height:21px}
.contact .c{width:52px;height:52px;border-radius:50%;background:var(--white);display:flex;align-items:center;justify-content:center;flex:none}
.field{position:absolute;left:810px;width:277px;height:36px;background:#3a3a3a;color:#ddd;font-size:11px;padding:11px 13px}
.send{left:810px;top:4164px;width:121px;height:34px;font-size:10px}
.foot-rule{left:110px;top:4154px;width:653px;height:1px;background:#4a4a4a}
.copy{left:110px;top:4173px;font-size:13px;color:var(--white)}
.social{position:absolute;top:4162px;width:36px;height:36px;border-radius:50%;border:2px solid var(--white)}
.social.first{background:var(--blue);border-color:var(--blue)}
</style>
</head>
<body>
<div class="page">

  <!-- top bar -->
  <div class="abs topbar">
    <div class="sep" style="left:112px"></div>
    <div class="item" style="left:131px">
      <svg width="12" height="12" viewBox="0 0 24 24"><path fill="#777" d="M6.6 10.8a15 15 0 0 0 6.6 6.6l2.2-2.2c.3-.3.7-.4 1-.2 1.1.4 2.3.6 3.6.6.6 0 1 .4 1 1V20c0 .6-.4 1-1 1A17 17 0 0 1 3 4c0-.6.4-1 1-1h3.5c.6 0 1 .4 1 1 0 1.3.2 2.5.6 3.6.1.3 0 .7-.2 1z"/></svg>
      (555) 304-7781</div>
    <div class="sep" style="left:268px"></div>
    <div class="item" style="left:289px">
      <svg width="10" height="13" viewBox="0 0 24 32"><path fill="#777" d="M12 0a11 11 0 0 0-11 11c0 8 11 21 11 21s11-13 11-21A11 11 0 0 0 12 0zm0 15a4 4 0 1 1 0-8 4 4 0 0 1 0 8z"/></svg>
      4180 Birch Hollow Rd, Alder Falls, MN 55392</div>
    <div class="sep" style="left:556px"></div>
    <div class="btn estimate">Free Estimate</div>
  </div>

  <!-- navigation -->
  <div class="abs nav">
    <div class="logo"><div class="mark"></div><div class="name">Brightmoor</div></div>
    <nav class="menu">
      <span class="dot"></span>
      <a class="active" style="left:437px">Home</a>
      <a style="left:495px">Services</a>
      <a style="left:577px">About Us</a>
      <a style="left:661px">FAQs</a>
      <a style="left:714px">Employment</a>
      <a style="left:821px">Testimonials</a>
      <a style="left:934px">Gallery</a>
      <a style="left:1011px">Contact Us</a>
    </nav>
  </div>

  <!-- hero -->
  <svg class="abs hero" viewBox="0 0 1200 644" width="1200" height="644">
    <defs>
      <linearGradient id="heroPhoto" x1="0" y1="0" x2="1" y2="0.3">
        <stop offset="0" stop-color="#38474b"/>
        <stop offset="0.45" stop-color="#4b5856"/>
        <stop offset="0.7" stop-color="#6f5d47"/>
        <stop offset="1" stop-color="#8a7054"/>
      </linearGradient>
    </defs>
    <path role="img" aria-label="Photo of two scuba divers clearing lake weeds beside a wooden dock" fill="url(#heroPhoto)" d="M0 0H1200V505Q600 769 0 505Z"/>
    <path fill="none" stroke="#0b6fc0" stroke-width="7" d="M0 512Q600 790 1200 500"/>
  </svg>
  <div class="abs hero-line"></div>
  <div class="abs hero-title">Keeping your shoreline<br>clean &amp; pristine</div>
  <div class="abs hero-sub">Along your dock, beach, or boat slip</div>
  <div class="btn hero-btn">Get Started</div>
  <div class="arrow" style="left:36px;top:364px"><svg width="10" height="14" viewBox="0 0 10 14"><path d="M8 1 2 7l6 6" fill="none" stroke="#0b6fc0" stroke-width="2.5"/></svg></div>
  <div class="arrow" style="left:1128px;top:364px"><svg width="10" height="14" viewBox="0 0 10 14"><path d="m2 1 6 6-6 6" fill="none" stroke="#0b6fc0" stroke-width="2.5"/></svg></div>

  <!-- about -->
  <h2 class="abs heading about-title"><span class="bold">About</span> <span class="light">Us</span></h2>
  <div class="abs about-text">
    <p>Brightmoor LLC is a company formed in response to the increase in invasive species in Minnesota lakes and waterways. The impact of these fast-growing nuisances inspired our venture to effectively control unwanted lake weeds and create an enjoyable environment craved by waterfront property homeowners.</p>
    <p>We have partnered with Greenleaf Compost Co. to recycle 100% of the lake weeds we remove. The types of materials used in compost have a huge impact on how long it takes to break down</p>
  </div>
  <div class="btn about-btn">Learn More</div>
  <div class="abs about-ring"></div>
  <div class="abs about-photo" role="img" aria-label="Photo of a covered boat lift at the end of a long wooden dock on a lake"></div>

  <!-- services -->
  <section class="abs services"></section>
  <h2 class="abs heading services-title"><span class="light">Our</span> <span class="bold">Services</span></h2>
  <div class="underline" style="top:1474px"></div>

  <div class="card" style="left:113px;top:1519px">
    <div class="photo" role="img" aria-label="Photo of a worker installing a dock beside a white boat" style="background:linear-gradient(180deg,#dfe6ea,#b9a48a)"></div>
    <div class="body">
      <div class="icon"><svg width="46" height="46" viewBox="0 0 46 46" fill="none" stroke="#fff" stroke-width="2.5"><circle cx="23" cy="23" r="14"/><circle cx="23" cy="23" r="6"/></svg></div>
      <h3>Dock install and<br>removal services</h3>
      <p>Broken bottles, cans, sticks, and sharp rocks are some examples of underwater nuisances that keep you from fully</p>
    </div>
  </div>
  <div class="card featured" style="left:448px;top:1519px">
    <div class="photo" role="img" aria-label="Close-up photo of zebra mussels on a rock" style="background:linear-gradient(180deg,#8a8a6a,#3e3a2c)"></div>
    <div class="body">
      <div class="icon"><svg width="46" height="46" viewBox="0 0 46 46" fill="none" stroke="#0b6fc0" stroke-width="2.5"><ellipse cx="23" cy="23" rx="17" ry="10"/><path d="M8 23h30"/></svg></div>
      <h3>Zebra mussel<br>removal</h3>
      <p>his Invasive species is becoming an increasing risk to Minnesota waterways. These sharp mussels build up</p>
    </div>
  </div>
  <div class="card" style="left:782px;top:1519px">
    <div class="photo" role="img" aria-label="Photo of a person picking up litter on a beach at sunset" style="background:linear-gradient(180deg,#f0c79a,#6a5448)"></div>
    <div class="body">
      <div class="icon"><svg width="46" height="46" viewBox="0 0 46 46" fill="none" stroke="#fff" stroke-width="2.5"><path d="M8 36q5-4 10 0t10 0 10 0M14 30h18M23 8v22"/></svg></div>
      <h3>Beach clean up<br>services</h3>
      <p>Continuous waves wash away sand from your beach to expose mud &amp; larger rocks. Consider touching up above</p>
    </div>
  </div>

  <div class="card" style="left:113px;top:1907px">
    <div class="photo" role="img" aria-label="Photo of a dock lift trailer parked outside a warehouse" style="background:linear-gradient(180deg,#9fb3c6,#5b5652)"></div>
    <div class="body">
      <div class="icon"><svg width="46" height="46" viewBox="0 0 46 46" fill="none" stroke="#fff" stroke-width="2.5"><path d="M10 12h26M23 12v26M16 38h14M30 12v10"/></svg></div>
      <h3>Dock lift<br>services</h3>
      <p>Our dive team has the ability to leave comb through sections and specifically target invasive plant species,</p>
    </div>
  </div>
  <div class="card" style="left:448px;top:1907px">
    <div class="photo" role="img" aria-label="Photo of clear shallow water beside a dock and kayaks" style="background:linear-gradient(180deg,#8fb0c4,#5f7a46)"></div>
    <div class="body">
      <div class="icon"><svg width="46" height="46" viewBox="0 0 46 46" fill="none" stroke="#fff" stroke-width="2.5"><path d="M10 38h26M23 38V14M16 38l-4-16M30 38l4-16"/></svg></div>
      <h3>Aquatic weed<br>removal</h3>
      <p>Reclaim open water in front of your dock, beach, or boat slip! Our removal method has teams of SCUBA divers</p>
    </div>
  </div>
  <div class="card" style="left:782px;top:1907px">
    <div class="photo" role="img" aria-label="Photo of scuba divers standing in a lake near a dock" style="background:linear-gradient(180deg,#7fa4c4,#3f5d74)"></div>
    <div class="body">
      <div class="icon"><svg width="46" height="46" viewBox="0 0 46 46" fill="none" stroke="#fff" stroke-width="2.5"><circle cx="26" cy="20" r="11"/><path d="M18 28 8 38"/></svg></div>
      <h3>Lost item<br>search</h3>
      <p>Have you dropped something of value in the water? From boat keys to tools to other items, our scuba divers</p>
    </div>
  </div>
  <div class="btn services-btn">View All Services</div>

  <!-- gallery -->
  <h2 class="abs heading gallery-title"><span class="light">Our</span> <span class="bold">Gallery</span></h2>
  <div class="underline" style="top:2543px"></div>
  <div class="shot" style="left:125px;width:231px;background:linear-gradient(180deg,#b8c7cf,#7b8a5a 55%,#9a8f7c)" role="img" aria-label="Before photo of a weed-covered wooden dock in tall reeds"></div>
  <div class="shot" style="left:361px;width:231px;background:linear-gradient(180deg,#6f8f4a,#8a9a6a 50%,#a59e8c)" role="img" aria-label="After photo of the same dock cleared of weeds"></div>
  <div class="shot" style="left:608px;width:232px;background:linear-gradient(180deg,#b5c1c7,#8c958a 55%,#6f7462)" role="img" aria-label="Before photo of lake water thick with floating weeds"></div>
  <div class="shot" style="left:845px;width:231px;background:linear-gradient(180deg,#c9d4dc,#8c9ca8 55%,#7d8b90)" role="img" aria-label="After photo of clear lake water beside a dock"></div>
  <div class="handle" style="left:336px"><svg width="20" height="10" viewBox="0 0 20 10"><path d="M6 0 0 5l6 5zM14 0l6 5-6 5z" fill="#999"/></svg></div>
  <div class="handle" style="left:818px"><svg width="20" height="10" viewBox="0 0 20 10"><path d="M6 0 0 5l6 5zM14 0l6 5-6 5z" fill="#999"/></svg></div>
  <div class="tag" style="left:680px">BEFORE</div>
  <div class="tag" style="left:917px">AFTER</div>
  <div class="arrow outline" style="left:36px;top:2711px"><svg width="10" height="14" viewBox="0 0 10 14"><path d="M8 1 2 7l6 6" fill="none" stroke="#0b6fc0" stroke-width="2.5"/></svg></div>
  <div class="arrow" style="left:1128px;top:2711px;background:var(--blue)"><svg width="10" height="14" viewBox="0 0 10 14"><path d="m2 1 6 6-6 6" fill="none" stroke="#fff" stroke-width="2.5"/></svg></div>

  <!-- innovators -->
  <svg class="abs innov" viewBox="0 0 1200 445" width="1200" height="445">
    <defs>
      <linearGradient id="innovPhoto" x1="0" y1="0" x2="0.6" y2="1">
        <stop offset="0" stop-color="#6f8d4c"/>
        <stop offset="0.5" stop-color="#4f6e3a"/>
        <stop offset="1" stop-color="#3a5530"/>
      </linearGradient>
    </defs>
    <rect width="1200" height="445" fill="#0b6fc0"/>
    <path role="img" aria-label="Photo of three scuba divers wading through a lily-pad covered lake" fill="url(#innovPhoto)" stroke="#fff" stroke-width="6" d="M-5 -5H520Q720 222 470 450H-5Z"/>
    <circle cx="599" cy="222" r="52" fill="rgba(255,255,255,.35)"/>
    <circle cx="599" cy="222" r="38" fill="#fff"/>
    <path d="M592 208v28l22-14z" fill="#0b6fc0"/>
  </svg>
  <div class="abs innov-title"><b>Aquatic innovators,</b><br><span>at your service</span></div>
  <div class="abs innov-line"></div>
  <div class="abs innov-text">Brightmoor LLC is a company formed in response to the increasing incidence of invasive species in Minnesota’s lakes and water systems. The impact of these fast-growing nuisances, inspired our venture to effectively control unwanted lake weeds. Brightmoor, LLC helps provide the enjoyable weed-free lake environment craved by water enthusiasts.</div>

  <!-- testimonials -->
  <h2 class="abs heading testi-title">Testimonials</h2>
  <div class="abs avatar-ring"></div>
  <div class="abs avatar" role="img" aria-label="Portrait photo of the reviewer by a lake"></div>
  <div class="abs quote-badge"><svg width="24" height="18" viewBox="0 0 24 18"><path d="M0 18V10Q0 2 8 0v4Q4 5 4 9h4v9zM13 18V10q0-8 8-10v4q-4 1-4 5h4v9z" fill="#fff"/></svg></div>
  <div class="abs testi-text">Everyone used to jump off the water trampoline and instantly get tangled in lake weeds. We contacted Brightmoor and their SCUBA divers have now been solving our problem for the past 4 years!”</div>
  <div class="abs testi-name">- Willow Bay Shores Association</div>
  <div class="abs testi-place">Lake Alder</div>
  <svg class="abs" style="left:966px;top:3656px" width="70" height="58" viewBox="0 0 24 18"><path d="M24 0v8q0 8-8 10v-4q4-1 4-5h-4V0zM11 0v8q0 8-8 10v-4q4-1 4-5H3V0z" fill="#e6e9ee"/></svg>
  <div class="abs dots"><i></i><i class="on"></i><i></i><i></i></div>

  <!-- footer -->
  <footer class="abs footer"></footer>
  <div class="abs footer-right"></div>

  <div class="foot-h" style="left:110px">Navigation</div>
  <ul class="foot-list" style="left:110px">
    <li><i></i>Home</li><li><i></i>Services</li><li><i></i>About Us</li><li><i></i>Testimonials</li><li><i></i>Gallery</li><li><i></i>Contact Us</li>
  </ul>
  <div class="foot-h" style="left:305px">Other Links</div>
  <ul class="foot-list" style="left:305px">
    <li><i></i>FAQs</li><li><i></i>Employment</li><li><i></i>Privacy Policy</li><li><i></i>Terms Of Use</li>
  </ul>
  <div class="foot-h" style="left:495px">Contact Info</div>
  <div class="contact" style="top:3946px">
    <div class="c"><svg width="14" height="18" viewBox="0 0 24 32"><path fill="#0b6fc0" d="M12 0a11 11 0 0 0-11 11c0 8 11 21 11 21s11-13 11-21A11 11 0 0 0 12 0zm0 15a4 4 0 1 1 0-8 4 4 0 0 1 0 8z"/></svg></div>
    <div>4180 Birch Hollow Rd<br>Alder Falls, MN 55392</div>
  </div>
  <div class="contact" style="top:4013px">
    <div class="c"><svg width="16" height="16" viewBox="0 0 24 24"><path fill="#0b6fc0" d="M6.6 10.8a15 15 0 0 0 6.6 6.6l2.2-2.2c.3-.3.7-.4 1-.2 1.1.4 2.3.6 3.6.6.6 0 1 .4 1 1V20c0 .6-.4 1-1 1A17 17 0 0 1 3 4c0-.6.4-1 1-1h3.5c.6 0 1 .4 1 1 0 1.3.2 2.5.6 3.6.1.3 0 .7-.2 1z"/></svg></div>
    <div>(555) 304-7781</div>
  </div>
  <div class="contact" style="top:4077px">
    <div class="c"><svg width="18" height="14" viewBox="0 0 18 14" fill="none" stroke="#0b6fc0" stroke-width="1.8"><rect x="1" y="1" width="16" height="12"/><path d="m1 1 8 7 8-7"/></svg></div>
    <div>hello@brightmoorllc.com</div>
  </div>

  <div class="foot-h" style="left:810px">Get In Touch</div>
  <div class="field" style="top:3949px">Your Name</div>
  <div class="field" style="top:3996px">Your Email</div>
  <div class="field" style="top:4044px">Subject</div>
  <div class="field" style="top:4092px;height:66px">Your Message</div>
  <div class="btn send">Send Message</div>

  <div class="abs foot-rule"></div>
  <div class="abs copy">© 2022 Brightmoor, LLC - All Rights Reserved</div>
  <div class="social first" style="left:574px" aria-label="Social profile"></div>
  <div class="social" style="left:617px" aria-label="Social profile"></div>
  <div class="social" style="left:659px" aria-label="Social profile"></div>
</div>
</body>
</html>
```